Home Staging Company needs business card design

We're a home staging company called Brightly Settled Home Staging. We would like a business card design that includes aqua and gray. Our current logo of house within chair is fine but I find we almost always use the logo in one color. I'll upload images of front and back of our current card and our logo. Note that we have dropped "Solutions" from our company name and don't want to include it on the card.

Target Market(s)

Realtors and homeowners - people interested in selling their homes

Contact Information for Business Card

Marisol Thistlewood
Brightly Settled Home Staging
757-555-0193
www.brightlysettled.com
marisol@brightlysettled.com

Font styles to use
Serif
Script

Requirements
Must have
• My logo and contact details
• UPDATE***
• I forgot to say that the company name should be included on the front of the card somehow.

```html
<!DOCTYPE html>
<html lang="en">
<head>
<meta charset="utf-8">
<title>Brightly Settled Home Staging – Business Cards</title>
<link rel="stylesheet" href="https://fonts.googleapis.com/css2?family=Merriweather:ital,wght@0,300;0,400;1,400&display=swap">
<style>
  :root {
    --backdrop: #101010;
    --aqua: #5fc7c4;
    --aqua-light: #76d3cf;
    --slate: #6d6d71;
    --slate-light: #807f84;
    --slate-dark: #5c5c60;
    --paper-white: #ffffff;
    --text-soft: #e9e9ea;
  }
  * { margin: 0; padding: 0; box-sizing: border-box; }
  html, body {
    width: 1200px; height: 1000px; overflow: hidden;
    background: var(--backdrop);
  }
  .stage {
    position: relative; width: 1200px; height: 1000px;
    display: flex; align-items: center; justify-content: center; gap: 60px;
  }
  .card {
    position: relative; width: 510px; height: 300px;
    border-radius: 22px; overflow: hidden;
    box-shadow: 0 18px 40px rgba(0,0,0,0.55);
  }

  /* Contact side */
  .card--contact { background: linear-gradient(135deg, var(--aqua-light), var(--aqua)); }
  .card--contact .panel { position: absolute; inset: 0; width: 100%; height: 100%; }
  .contact-block {
    position: absolute; left: 0; right: 0; top: 34px;
    text-align: center; color: var(--paper-white);
    font-family: "Merriweather", Georgia, serif;
  }
  .mark-small { display: flex; align-items: center; justify-content: center; gap: 8px; }
  .mark-dot { width: 22px; height: 22px; border-radius: 50%; background: var(--aqua); }
  .mark-name { font-size: 11px; font-weight: 400; letter-spacing: 0.5px; color: var(--aqua-light); }
  .person-name {
    margin-top: 18px; font-size: 21px; font-style: italic; font-weight: 400; letter-spacing: 0.3px;
  }
  .rule { width: 150px; height: 1px; background: var(--text-soft); margin: 16px auto 18px; }
  .contact-line { font-size: 12.5px; font-weight: 300; line-height: 1.55; color: var(--text-soft); }

  /* Brand side */
  .card--brand {
    background: linear-gradient(135deg, var(--slate-light), var(--slate) 55%, var(--slate-dark));
    display: flex; flex-direction: column; align-items: center; justify-content: center;
    font-family: "Merriweather", Georgia, serif; color: var(--paper-white);
  }
  .brand-dot { width: 74px; height: 74px; border-radius: 50%; background: var(--aqua); }
  .brand-name { margin-top: 22px; font-size: 26px; font-weight: 400; text-align: center; line-height: 1.3; }
</style>
</head>
<body>
<main class="stage">
  <section class="card card--contact" aria-label="Contact side of the card">
    <svg class="panel" viewBox="0 0 510 300" preserveAspectRatio="none" aria-hidden="true">
      <polygon points="128,-4 382,-4 468,150 382,304 128,304 42,150"
               fill="var(--slate)" stroke="var(--paper-white)" stroke-width="3"/>
    </svg>
    <div class="contact-block">
      <div class="mark-small">
        <span class="mark-dot"></span>
        <span class="mark-name">Brightly Settled Home Staging</span>
      </div>
      <h1 class="person-name">Marisol Thistlewood</h1>
      <div class="rule"></div>
      <p class="contact-line">757-555-0193</p>
      <p class="contact-line">www.brightlysettled.com</p>
      <p class="contact-line">marisol@brightlysettled.com</p>
    </div>
  </section>

  <section class="card card--brand" aria-label="Brand side of the card">
    <span class="brand-dot"></span>
    <h2 class="brand-name">Brightly Settled<br>Home Staging</h2>
  </section>
</main>
</body>
</html>
```